Expedition Cruise Sales Website for the Polar Regions (Antarctica & Arctic)

This will be a website for selling cruises.
This site should have a homepage, a ship page, destinations, and itineraries.
I have created a file specifying each page, and it is attached.
Pages:
1. Home
2. Cruise Lines
- 2.1 Ships
3. Destinations
- 3.1 Region - 3.2 Country - 3.3 City
4. Itineraries
- 4.1 Itinerary
5. Blog / Travel Tips 6. About Us
7. Contact
Please take a look on the attached pdf
Target Market(s)
Expedition Travelers
Coding
Coded - Design and coding required
Number of Pages Required
5+ page
Font styles to use
Look and feel
Each slider illustrates characteristics of the customer's brand and the style your logo design should communicate.

```html
<!DOCTYPE html>
<html lang="en">
<head>
<meta charset="utf-8">
<title>Borealis.co — Expedition Cruises</title>
<link rel="stylesheet" href="https://fonts.googleapis.com/css2?family=Bebas+Neue&family=Plus+Jakarta+Sans:wght@400;500;600;700;800&display=swap">
<style>
  :root{
    --blue:#1459b8;
    --blue-dark:#0f4b9c;
    --heading-blue:#1a62c4;
    --ink:#141414;
    --muted:#3a3a3a;
    --card:#f4f5f7;
    --line:#cfd4dc;
    --footer:#0b0b0c;
    --white:#ffffff;
    --sea:#1f5e97;
  }
  *{box-sizing:border-box;margin:0;padding:0}
  html,body{width:1200px;height:3615px;overflow:hidden;background:var(--white)}
  body{position:relative;font-family:"Plus Jakarta Sans",sans-serif;color:var(--ink)}
  .abs{position:absolute}
  .display{font-family:"Bebas Neue",sans-serif;font-weight:400;letter-spacing:.5px}

  /* nav */
  .brand-mark{left:44px;top:38px;font-weight:800;font-size:22px;color:var(--ink)}
  .nav{right:42px;top:43px;display:flex;gap:34px;font-size:18px;font-weight:500}

  /* hero */
  .hero{left:42px;top:108px;width:1116px;height:549px;border-radius:20px;overflow:hidden;
    background:linear-gradient(180deg,#1677e6 0%,#2a8df0 45%,#e9eef4 62%,#d2dbe4 75%,#1aa8d6 100%)}
  .hero-title{left:58px;top:44px;font-size:56px;line-height:62px;color:var(--white)}
  .hero-sub{right:58px;top:52px;width:400px;text-align:right;font-size:18px;font-weight:700;line-height:24px;color:var(--white)}

  .search{left:74px;top:582px;width:1050px;height:151px;background:var(--white);border-radius:16px;
    box-shadow:0 4px 18px rgba(0,0,0,.12)}
  .field{position:absolute;top:34px;width:263px}
  .field label{display:block;font-size:19px;font-weight:500;margin-bottom:11px}
  .select{height:48px;border:1px solid var(--line);border-radius:6px;padding:0 16px;display:flex;align-items:center;justify-content:space-between;font-size:14px;color:#9aa0a8}
  .btn{background:var(--blue);color:var(--white);font-weight:700;border-radius:6px;display:flex;align-items:center;justify-content:center}
  .search .btn{position:absolute;left:872px;top:69px;width:146px;height:48px;font-size:15px}

  /* section heads */
  .eyebrow{font-size:23px;font-weight:500}
  .section-title{font-size:36px;font-weight:700;color:var(--heading-blue);letter-spacing:-.3px}
  .see-more{width:115px;height:48px;font-size:14px}

  /* itinerary cards */
  .trip{top:888px;width:355px;height:670px;background:var(--card);border-radius:14px;overflow:hidden}
  .trip-photo{height:355px;border-radius:14px}
  .trip-body{padding:26px 25px 0}
  .trip h3{font-size:23px;font-weight:700;margin-bottom:14px}
  .trip p{font-size:17.5px;line-height:23.5px;color:var(--muted);height:70px}
  .tags{display:flex;gap:8px;margin-top:14px}
  .tag{background:var(--blue);color:var(--white);font-size:14px;font-weight:700;padding:4px 12px;border-radius:5px}
  .from{font-size:19px;font-weight:500;margin-top:30px}
  .price{font-size:54px;line-height:60px;color:var(--blue);margin-top:4px}

  /* explore band */
  .explore{left:0;top:1610px;width:1200px;height:565px;background:radial-gradient(ellipse at 60% 50%,#2a6fad 0%,#1c578f 55%,#143f6c 100%)}
  .explore-title{left:100px;top:86px;font-size:58px;line-height:62px;color:var(--white)}
  .explore-text{left:100px;top:283px;width:340px;font-size:22px;line-height:28.5px;font-weight:500;color:var(--white)}
  .dest{top:83px;width:224px;height:400px;border-radius:12px;overflow:hidden;text-align:center;color:var(--white)}
  .dest small{position:absolute;top:170px;left:0;right:0;font-size:14px;font-style:italic;opacity:.9}
  .dest b{position:absolute;top:188px;left:0;right:0;font-family:"Bebas Neue",sans-serif;font-weight:400;font-size:36px}
  .dest-rail{left:1067px;top:83px;width:33px;height:400px;background:#ececec;display:flex;align-items:center;justify-content:center}

  /* testimonials */
  .review{top:2331px;width:500px;height:298px;background:var(--card);border-radius:18px;padding:24px 25px}
  .avatar{position:absolute;left:25px;top:24px;width:67px;height:67px;border-radius:50%}
  .review h4{margin-left:84px;font-size:23px;font-weight:700;margin-top:6px}
  .stars{margin-left:84px;margin-top:4px;display:flex;gap:3px}
  .review p{margin-top:28px;font-size:18px;line-height:23.5px;color:var(--muted)}

  /* footer */
  .footer{left:42px;top:2797px;width:1116px;height:800px;background:var(--footer);border-radius:0 0 20px 20px;color:var(--white)}
  .connect{left:74px;top:2681px;width:1050px;height:231px;border-radius:22px;overflow:hidden;
    background:linear-gradient(100deg,#2f5d6e 0%,#4e7f8a 35%,#86a4a4 60%,#a8a094 80%,#6e6a62 100%)}
  .connect h2{position:absolute;left:51px;top:42px;font-size:56px;line-height:56px;color:var(--white)}
  .connect .sub{position:absolute;left:51px;top:105px;font-size:23px;color:var(--white)}
  .pill{position:absolute;top:147px;height:46px;background:var(--white);border-radius:6px;display:flex;align-items:center;gap:10px;padding:0 24px;font-size:14px;font-weight:700;color:var(--ink)}
  .quick h3,.news h3{font-size:28px;font-weight:700}
  .links{display:flex;gap:0;margin-top:24px}
  .links ul{list-style:none;width:223px}
  .links li{font-size:23px;line-height:45px}
  .input{margin-top:26px;width:400px;height:48px;border:1px solid #5a5a5a;border-radius:6px;display:flex;overflow:hidden}
  .input span{flex:1;display:flex;align-items:center;padding-left:16px;font-size:14px;color:#cfcfcf}
  .input .btn{width:100px;font-size:15px;border-radius:6px}
  .lang{margin-top:16px;width:400px;height:48px;border:1px solid #5a5a5a;border-radius:6px;display:flex;align-items:center;justify-content:space-between;padding:0 16px;font-size:14px;color:#e6e6e6}
  .social{display:flex;gap:8px;margin-top:24px}
  .social i{width:49px;height:49px;border:2px solid var(--white);border-radius:50%;display:block}
  .foot-brand{left:0;width:1116px;text-align:center}
</style>
</head>
<body>

<header>
  <div class="abs brand-mark">Borealis.co</div>
  <nav class="abs nav">
    <span>Find the Cruise</span><span>Ships</span><span>Destinations</span><span>Itineraries</span><span>Blog</span><span>Contact Us</span>
  </nav>
</header>

<section class="abs hero" role="img" aria-label="Large white cruise ship docked under a bright blue sky beside a sandy beach">
  <h1 class="abs hero-title display">Enjoy your trip<br>with the best cruise</h1>
  <p class="abs hero-sub">Discover cruises that are innovative, elegant, and offer you maximum comfort</p>
</section>

<form class="abs search">
  <div class="field" style="left:34px"><label>Cruising to</label><div class="select">Choose your destination <svg width="14" height="9" viewBox="0 0 14 9"><path d="M1 1l6 6 6-6" fill="none" stroke="#222" stroke-width="2"/></svg></div></div>
  <div class="field" style="left:313px"><label>Leaving from</label><div class="select">Choose a departure point <svg width="14" height="9" viewBox="0 0 14 9"><path d="M1 1l6 6 6-6" fill="none" stroke="#222" stroke-width="2"/></svg></div></div>
  <div class="field" style="left:593px"><label>Leaving on</label><div class="select">Choose the date <svg width="14" height="9" viewBox="0 0 14 9"><path d="M1 1l6 6 6-6" fill="none" stroke="#222" stroke-width="2"/></svg></div></div>
  <div class="btn">Search Cruise</div>
</form>

<section>
  <div class="abs eyebrow" style="left:42px;top:783px">itineraries</div>
  <h2 class="abs section-title" style="left:42px;top:820px">Find Your Best Journey</h2>
  <div class="abs btn see-more" style="left:1043px;top:808px">See More</div>

  <article class="abs trip" style="left:42px">
    <div class="trip-photo" role="img" aria-label="Snowy Antarctic mountains reflected in calm water" style="background:linear-gradient(180deg,#4f86c9 0%,#b9cbe0 40%,#6f7f93 60%,#1f2a36 100%)"></div>
    <div class="trip-body">
      <h3>Best Antarctic Cruises</h3>
      <p>A Once-in-a-lifetime adventure for the brave who want to explore the white continent. Depart from Us...</p>
      <div class="tags"><span class="tag">Adventure</span><span class="tag">Polar Regions</span></div>
      <div class="from">Starts from</div>
      <div class="price display">$8500</div>
    </div>
  </article>

  <article class="abs trip" style="left:422px">
    <div class="trip-photo" role="img" aria-label="Expedition ship beside rugged reddish volcanic cliffs" style="background:linear-gradient(160deg,#7b5a45 0%,#a9704d 45%,#6e4f3c 70%,#2d4a6a 100%)"></div>
    <div class="trip-body">
      <h3>Top Galápagos Cruises</h3>
      <p>It's a journey to see the world through the eyes of a naturalist, coming face-to-face with its am...</p>
      <div class="tags"><span class="tag">Adventure</span><span class="tag">Nature</span></div>
      <div class="from">Starts from</div>
      <div class="price display">$7200</div>
    </div>
  </article>

  <article class="abs trip" style="left:803px">
    <div class="trip-photo" role="img" aria-label="City skyline of tall towers behind a river cruise boat" style="background:linear-gradient(180deg,#9bb9d9 0%,#6e7e90 45%,#3f4d5c 75%,#5c7488 100%)"></div>
    <div class="trip-body">
      <h3>Last-Minute Deals</h3>
      <p>We offer a selection of cruise deals to visit cities that are at the top of the bucket list. Last -minute cruis...</p>
      <div class="tags"><span class="tag">Vacation</span><span class="tag">Cities</span></div>
      <div class="from">Starts from</div>
      <div class="price display">$420</div>
    </div>
  </article>
</section>

<section class="abs explore" role="img" aria-label="Aerial view of deep blue ocean water">
  <h2 class="abs explore-title display">Explore more<br>than 300<br>place to visit</h2>
  <p class="abs explore-text">Cruising with us unlocks some of the world's best and most iconic corners. With us, there are no limits to adventure as we have round-the-world itineraries that sail to over 300 stunning ports of call.</p>
  <div class="abs dest" style="left:486px;background:linear-gradient(180deg,#3f8a8f 0%,#7fa9a0 50%,#8b8a7a 100%)" role="img" aria-label="Aerial view of a Caribbean shoreline with palm trees"><small>Destionations</small><b>CARIBBEAN</b></div>
  <div class="abs dest" style="left:719px;background:linear-gradient(180deg,#5e9a8a 0%,#3f8f98 50%,#2b6f86 100%)" role="img" aria-label="Aerial view of Maldives island with overwater villas"><small>Destionations</small><b>MALDIVES</b></div>
  <div class="abs dest" style="left:953px;width:114px;border-radius:12px 0 0 12px;background:linear-gradient(180deg,#2f6a78 0%,#1f4f5e 100%)" role="img" aria-label="Aerial view of Bahamas coastline"><small style="left:64px;text-align:left">Destion</small><b style="left:42px;text-align:left">BAHA</b></div>
  <div class="abs dest-rail"><svg width="10" height="14" viewBox="0 0 10 14"><path d="M2 1l6 6-6 6" fill="none" stroke="#111" stroke-width="2"/></svg></div>
</section>

<section>
  <div class="abs eyebrow" style="left:42px;top:2227px">Testimonials</div>
  <h2 class="abs section-title" style="left:42px;top:2263px">People talk About Us</h2>
  <div class="abs btn see-more" style="left:1043px;top:2251px">See More</div>

  <article class="abs review" style="left:42px">
    <div class="avatar" role="img" aria-label="Portrait of a customer" style="background:linear-gradient(135deg,#8aa3b8,#5b6f57)"></div>
    <h4>Clara Whitfield</h4>
    <div class="stars"><svg width="120" height="20" viewBox="0 0 120 20" fill="#f4b400"><g id="s"><path d="M10 1l2.6 6 6.4.5-4.9 4.2 1.5 6.3L10 14.7 4.4 18l1.5-6.3L1 7.5 7.4 7z"/></g><use href="#s" x="25"/><use href="#s" x="50"/><use href="#s" x="75"/><use href="#s" x="100"/></svg></div>
    <p>“My family and I just returned from a trip with Aurelia Cruise, and it felt like a dream! From the outstanding service to the luxurious facilities, everything was perfect. The kids had a blast with all the activities available. Thank you, for giving us an amazing vacation. We will definitely be back!.”</p>
  </article>

  <article class="abs review" style="left:559px">
    <div class="avatar" role="img" aria-label="Portrait of a customer" style="background:linear-gradient(135deg,#c9d3dd,#6b5446)"></div>
    <h4>Maya Okafor</h4>
    <div class="stars"><svg width="120" height="20" viewBox="0 0 120 20" fill="#f4b400"><use href="#s"/><use href="#s" x="25"/><use href="#s" x="50"/><use href="#s" x="75"/><use href="#s" x="100"/></svg></div>
    <p>“I never imagined how relaxing a cruise vacation could be until I experienced it myself! From a cozy room with a private balcony to an incredibly soothing spa, everything helped me unwind completely. I highly recommend it to anyone looking for a hassle-free getaway!”</p>
  </article>

  <article class="abs review" style="left:1075px;width:160px;border-radius:18px 0 0 18px">
    <div class="avatar" role="img" aria-label="Portrait of a customer" style="background:linear-gradient(135deg,#3b8f5a,#c07b6a)"></div>
    <p style="margin-top:85px;white-space:nowrap;overflow:hidden">I've been<br>to my dream<br>Waking up to<br>world-class<br>destinations<br>unpacked</p>
  </article>
</section>

<footer>
  <div class="abs footer">
    <div class="abs quick" style="left:58px;top:170px">
      <h3>Quick Link</h3>
      <div class="links">
        <ul><li>Home</li><li>Cruise Line</li><li>Ships</li><li>Destination</li><li>Itineraries</li><li>Blog</li><li>About Us</li></ul>
        <ul><li>Terms &amp; Conditions</li><li>FAQ</li><li>Contact</li><li>Privacy Policy</li><li>Whistleblower</li></ul>
      </div>
    </div>
    <div class="abs news" style="left:658px;top:170px">
      <h3>Subscribe to Our Newsletter</h3>
      <div class="input"><span>Insert your Email Address</span><div class="btn">Submit</div></div>
      <div class="lang">Corporate | English <svg width="14" height="9" viewBox="0 0 14 9"><path d="M1 1l6 6-6 6" fill="none" stroke="#fff" stroke-width="2" transform="rotate(90 7 4.5) translate(2 -2)"/></svg></div>
      <h3 style="margin-top:58px">Follow us on</h3>
      <div class="social" aria-label="Social media links"><i></i><i></i><i></i><i></i><i></i><i></i></div>
    </div>
    <div class="abs foot-brand" style="top:577px">
      <div style="width:64px;height:64px;border-radius:50%;background:var(--white);margin:0 auto"></div>
      <div style="font-size:42px;font-weight:700;margin-top:20px">Borealis.co</div>
      <div style="font-size:22px;margin-top:14px">© 2025 Borealis.co. All rights reserved.</div>
    </div>
  </div>

  <div class="abs connect" role="img" aria-label="Traveller sitting on seaside rocks looking out over the ocean">
    <h2 class="display">Let's connect</h2>
    <div class="sub">Before Your Next Journey</div>
    <div class="pill" style="left:51px"><svg width="18" height="18"><circle cx="9" cy="9" r="9" fill="#25a244"/></svg>Contact Us on ChatLine</div>
    <div class="pill" style="left:311px"><svg width="20" height="16"><rect width="20" height="16" rx="2" fill="var(--blue)"/></svg>Subscribe to Our Newsletter</div>
  </div>
</footer>

</body>
</html>
```